Business Card Design Project : Ridgeline Press

In preparation for market launch, Tamarind's Ridgeline Press require the development of a business card. Ridgeline Press is a Community online publishing web portal. We provide the the city of Whistler located in B.C. (Canada) business directories, News, Classified ads, News, Events and blogs etc.

The main focus of the brand is to help local businesses to corporate with their online advertisement and marketing. Meeting our clients face to face is a must (B2B).

Target Market(s)

The target market is B2B customers. Business Owners to Marketing, advertising Managers

Industry/Entity Type

Business

Requirements
Must have
• - The business card will be two sided.
the BACK side will have our logo which consist of (icon, url,slogan) submited. The logo will be middle and centred.

The FRONT side should have company details:

Company Legal Name: TAMARIND RIDGELINE MEDIA

Owen Farsk
Director of Sales & Marketing

www.tamarindridgeline.biz
owen@tamarindridgeline.biz

Phone: 604 317 8842
#2714 - 582 E. Halvern St.
Vancouver, B.C. V7K2R4 Canada
Nice to have
• - For the "FRONT" side of our business card. You can separate or re-arrange with our logo components (icon, logo,slogan). It does not have to be together.

Also our company legal name is rather long so arrange or organize the name in a way to make it shorter. Your experience and creativity will have to come in play.
Should not have
• should not have other colors beside logo color and black text (2 colors). Also nothing Three dimensional

```html
<!DOCTYPE html>
<html lang="en">
<head>
<meta charset="utf-8">
<title>Ridgeline Press — Business Card</title>
<link href="https://fonts.googleapis.com/css2?family=Open+Sans:wght@400;600;700&display=swap" rel="stylesheet">
<style>
  :root {
    --brand-blue: #1f6fb5;
    --brand-blue-dark: #17598f;
    --ink: #161616;
    --band: #231f1e;
    --paper: #ffffff;
    --stage: #e9eaec;
    --muted: #c9cbcf;
  }
  * { box-sizing: border-box; margin: 0; padding: 0; }
  html, body { width: 1200px; height: 944px; overflow: hidden; }
  body {
    background: var(--stage);
    font-family: "Open Sans", Arial, sans-serif;
    color: var(--ink);
    position: relative;
  }
  .card {
    position: absolute;
    width: 620px;
    height: 354px;
    background: var(--paper);
    border-radius: 22px;
    overflow: hidden;
  }

  /* Back side: centred logo block */
  .card-back { left: 90px; top: 80px; }
  .back-logo {
    position: absolute; inset: 0;
    display: flex; flex-direction: column; align-items: center; justify-content: center;
  }
  .brand-name {
    display: flex; align-items: center; gap: 14px;
    font-weight: 700; font-size: 44px; color: var(--brand-blue);
    margin-bottom: 18px;
  }
  .brand-square { width: 30px; height: 30px; background: var(--brand-blue); }
  .back-url { font-weight: 700; font-size: 38px; letter-spacing: -0.5px; line-height: 1; }
  .back-slogan { font-size: 27px; color: var(--brand-blue); margin-top: 4px; }

  /* Front side: details */
  .card-front { left: 490px; top: 500px; }
  .front-swoosh { position: absolute; left: 0; top: 0; width: 620px; height: 354px; }
  .front-brand {
    position: absolute; left: 46px; top: 58px;
  }
  .front-brand .brand-name { font-size: 28px; gap: 10px; margin-bottom: 10px; }
  .front-brand .brand-square { width: 20px; height: 20px; }
  .front-slogan { font-size: 17px; color: var(--ink); }
  .person { position: absolute; left: 364px; top: 38px; }
  .person-name { font-size: 20px; }
  .person-title { font-size: 13px; color: var(--brand-blue); }
  .contact-list { position: absolute; left: 364px; top: 122px; list-style: none; font-size: 14px; line-height: 1.25; }
  .contact-list li { display: flex; align-items: flex-start; gap: 8px; margin-bottom: 8px; }
  .contact-list svg { flex: none; margin-top: 2px; }
  .front-url {
    position: absolute; left: 0; right: 0; top: 290px;
    text-align: center; color: var(--paper);
    font-size: 19px; letter-spacing: 2px;
  }
</style>
</head>
<body>

  <section class="card card-back" aria-label="Business card back">
    <div class="back-logo">
      <div class="brand-name"><span class="brand-square"></span>Ridgeline Press</div>
      <div class="back-url">www.tamarindridgeline.biz</div>
      <div class="back-slogan">Your information gateway</div>
    </div>
  </section>

  <section class="card card-front" aria-label="Business card front">
    <svg class="front-swoosh" viewBox="0 0 620 354" aria-hidden="true">
      <path d="M0 210 C170 240 420 250 620 190 L620 354 L0 354 Z" fill="var(--brand-blue)"/>
      <path d="M0 222 C170 256 420 268 620 212 L620 354 L0 354 Z" fill="var(--muted)"/>
      <path d="M0 232 C170 270 420 284 620 236 L620 354 L0 354 Z" fill="var(--band)"/>
    </svg>

    <div class="front-brand">
      <div class="brand-name"><span class="brand-square"></span>Ridgeline Press</div>
      <div class="front-slogan">Your information gateway</div>
    </div>

    <div class="person">
      <div class="person-name">Owen Farsk</div>
      <div class="person-title">Director of Sales &amp; Marketing</div>
    </div>

    <ul class="contact-list">
      <li>
        <svg width="13" height="12" viewBox="0 0 13 12"><path d="M6.5 0 L13 6 H11 V12 H8 V8 H5 V12 H2 V6 H0 Z" fill="var(--brand-blue)"/></svg>
        <span>#2714 - 582 E. Halvern St.<br>Vancouver, B.C. V7K2R4 Canada</span>
      </li>
      <li>
        <svg width="13" height="13" viewBox="0 0 13 13"><circle cx="6.5" cy="6.5" r="6" fill="none" stroke="var(--brand-blue)" stroke-width="1.5"/><path d="M4 3.5 L5.5 3.5 L6 5.5 L5 6.2 C5.5 7.3 6 7.8 7 8.2 L7.7 7.2 L9.5 7.7 L9.5 9.2 C6.5 9.5 3.8 6.8 4 3.5 Z" fill="var(--brand-blue)"/></svg>
        <span>604 317 8842</span>
      </li>
      <li>
        <svg width="14" height="11" viewBox="0 0 14 11"><rect x="0.5" y="0.5" width="13" height="10" fill="var(--brand-blue)"/><path d="M0.5 0.5 L7 6 L13.5 0.5" fill="none" stroke="#fff" stroke-width="1.2"/></svg>
        <span>owen@tamarindridgeline.biz</span>
      </li>
    </ul>

    <div class="front-url">www.tamarindridgeline.biz</div>
  </section>

</body>
</html>
```